Copper lark buildworks

Copper lark buildworks is a small construction company.
Who is a licenced builder, Carpenter, joiner,
working on heritage ,new build, speacial projects and sometimes furniture

Industry/Entity Type

Construction

```html
<!DOCTYPE html>
<html lang="en">
<head>
<meta charset="utf-8">
<title>Copper lark buildworks – Business Card</title>
<link href="https://fonts.googleapis.com/css2?family=Oswald:wght@500;600&family=Arimo:wght@400&display=swap" rel="stylesheet">
<style>
  :root {
    --page-bg: #e9e9e9;
    --card-bg: #ffffff;
    --brand-green: #62b666;
    --text-grey: #4a4a4a;
    --muted-grey: #6b6b6b;
    --divider-grey: #b9b9b9;
  }
  html, body {
    margin: 0;
    padding: 0;
    width: 1200px;
    height: 900px;
    overflow: hidden;
    background: var(--page-bg);
  }
  .business-card {
    position: absolute;
    left: 100px;
    top: 164px;
    width: 1000px;
    height: 572px;
    background: var(--card-bg);
    border-radius: 22px;
    box-shadow: 0 10px 30px rgba(0,0,0,0.12);
  }
  .company-name {
    position: absolute;
    left: 0;
    right: 0;
    top: 170px;
    margin: 0;
    text-align: center;
    padding-left: 110px;
    font-family: "Oswald", sans-serif;
    font-weight: 600;
    font-size: 66px;
    letter-spacing: -0.5px;
    color: var(--brand-green);
  }
  .person-block {
    position: absolute;
    right: 560px;
    top: 372px;
    text-align: right;
  }
  .person-name {
    margin: 0;
    font-family: "Oswald", sans-serif;
    font-weight: 600;
    font-size: 44px;
    line-height: 1.1;
    color: var(--brand-green);
  }
  .person-role {
    margin: 0;
    font-family: "Arimo", sans-serif;
    font-size: 28px;
    color: var(--muted-grey);
  }
  .divider {
    position: absolute;
    left: 466px;
    top: 384px;
    width: 3px;
    height: 78px;
    background: var(--divider-grey);
  }
  .contact-list {
    position: absolute;
    left: 500px;
    top: 384px;
    margin: 0;
    padding: 0;
    list-style: none;
    font-family: "Arimo", sans-serif;
    font-size: 29px;
    color: var(--text-grey);
  }
  .contact-item {
    display: flex;
    align-items: center;
    gap: 14px;
    height: 40px;
  }
  .contact-icon {
    width: 28px;
    height: 28px;
    fill: var(--brand-green);
    flex: none;
  }
</style>
</head>
<body>
  <div class="business-card">
    <h1 class="company-name">Copper lark buildworks</h1>

    <div class="person-block">
      <p class="person-name">Warren Holt</p>
      <p class="person-role">Owner</p>
    </div>

    <div class="divider"></div>

    <ul class="contact-list">
      <li class="contact-item">
        <svg class="contact-icon" viewBox="0 0 24 24" aria-hidden="true">
          <path d="M6.6 10.8c1.4 2.8 3.8 5.1 6.6 6.6l2.2-2.2c.3-.3.7-.4 1-.2 1.1.4 2.3.6 3.6.6.6 0 1 .4 1 1V20c0 .6-.4 1-1 1C10.6 21 3 13.4 3 4c0-.6.4-1 1-1h3.5c.6 0 1 .4 1 1 0 1.3.2 2.5.6 3.6.1.3 0 .7-.2 1l-2.3 2.2z"/>
        </svg>
        <span>555 210 4873</span>
      </li>
      <li class="contact-item">
        <svg class="contact-icon" viewBox="0 0 24 24" aria-hidden="true">
          <path d="M2 5h20v2l-10 6L2 7z"/>
          <path d="M2 9l10 6 10-6v10H2z"/>
        </svg>
        <span>hello@copperlark.com</span>
      </li>
    </ul>
  </div>
</body>
</html>
```